Quillmere Air Business Card Design

Design new, 2 sides, business cards for a residential and light commercial heating, air conditioning contractor.

Target Market(s)

Homeowners, small businesses

Industry/Entity Type

Business

Contact Information for Business Card

Dominic Westerhall
Phone - 862-415-2736
Email
Address - PO box 518
Brightwater NJ 07912
Website - www.QuillmereAirLLC.example

Requirements
Must have
• logo, company colors, standard size with no die cut, so I can use nova stamp

```html
<!DOCTYPE html>
<html lang="en">
<head>
<meta charset="utf-8">
<title>Quillmere Air Business Card</title>
<link href="https://fonts.googleapis.com/css2?family=Lato:wght@400;700&display=swap" rel="stylesheet">
<style>
  :root {
    --maroon: #9e2235;
    --paper: #ffffff;
    --ink: #555555;
    --stage: #e9e6e1;
  }
  * { box-sizing: border-box; margin: 0; padding: 0; }
  html, body { width: 1200px; height: 903px; overflow: hidden; }
  body {
    background: var(--stage);
    font-family: "Lato", sans-serif;
    display: flex;
    align-items: center;
    justify-content: center;
    gap: 50px;
  }
  .card {
    position: relative;
    width: 525px;
    height: 300px;
    box-shadow: 0 6px 18px rgba(0,0,0,0.18);
    overflow: hidden;
  }
  .card-front { background: var(--maroon); color: var(--paper); }
  .card-back { background: var(--paper); }

  .brand {
    display: flex;
    align-items: center;
    gap: 10px;
    font-weight: 700;
    white-space: nowrap;
  }
  .brand-dot { width: 18px; height: 18px; border-radius: 50%; }
  .card-front .brand {
    position: absolute; left: 50%; top: 112px; transform: translateX(-50%);
    font-size: 38px; color: var(--paper);
  }
  .card-front .brand-dot { background: var(--paper); }
  .front-web {
    position: absolute; left: 0; right: 0; bottom: 34px;
    text-align: center; font-size: 15px; letter-spacing: 0.3px;
  }

  .card-back .brand {
    position: absolute; right: 32px; top: 40px;
    font-size: 26px; color: var(--maroon);
  }
  .card-back .brand-dot { width: 14px; height: 14px; background: var(--maroon); }
  .holder {
    position: absolute; left: 34px; top: 138px;
    font-size: 22px; font-weight: 700; color: var(--maroon);
  }
  .contacts {
    position: absolute; left: 34px; top: 174px;
    list-style: none; font-size: 14px; color: var(--ink);
  }
  .contacts li { display: flex; align-items: center; gap: 12px; height: 20px; }
  .contacts svg { width: 12px; height: 12px; fill: var(--maroon); flex: none; }
  .address-band {
    position: absolute; left: 0; right: 0; bottom: 0; height: 46px;
    background: var(--maroon); color: var(--paper);
    display: flex; align-items: center; justify-content: flex-end;
    padding-right: 34px; font-size: 15px;
  }
</style>
</head>
<body>
  <section class="card card-front">
    <div class="brand"><span class="brand-dot"></span>Quillmere Air</div>
    <p class="front-web">www.QuillmereAirLLC.example</p>
  </section>

  <section class="card card-back">
    <div class="brand"><span class="brand-dot"></span>Quillmere Air</div>
    <h1 class="holder">Dominic Westerhall</h1>
    <ul class="contacts">
      <li>
        <svg viewBox="0 0 12 12"><path d="M2.5 0.5 L4.5 0.5 L5.2 3.2 L3.8 4.3 Q4.8 6.8 7.7 8.2 L8.8 6.8 L11.5 7.5 L11.5 9.5 Q11.5 11.5 9.5 11.5 Q0.5 10.5 0.5 2.5 Q0.5 0.5 2.5 0.5 Z"/></svg>
        862-415-2736
      </li>
      <li>
        <svg viewBox="0 0 12 12"><path d="M0.5 2 H11.5 V10 H0.5 Z M1.2 2.6 L6 6.4 L10.8 2.6" fill="none" stroke="#9e2235" stroke-width="1.2"/></svg>
        info@QuillmereAirLLC.example
      </li>
      <li>
        <svg viewBox="0 0 12 12"><circle cx="6" cy="6" r="5.2" fill="none" stroke="#9e2235" stroke-width="1.1"/><path d="M0.8 6 H11.2 M6 0.8 Q2.8 6 6 11.2 M6 0.8 Q9.2 6 6 11.2" fill="none" stroke="#9e2235" stroke-width="0.9"/></svg>
        www.QuillmereAirLLC.example
      </li>
    </ul>
    <div class="address-band">PO box 518, Brightwater NJ 07912</div>
  </section>
</body>
</html>
```